Need A Standard Musical Download Website

We are looking for a talented designer to create a unique web design for our startup Music website called Vorde Sound.
The website should be responsive and filled with some creative stuffs along with bright colors.

Vorde sound is a website loaded with different types of music and capable of downloading the requested music by its users.
There will be categories of music which would be sorted by the genre. They include RnB, Hip-Hop, Afro pop, Pop, Dancehall and Reggae).

DESIGN STYLE/THEME

Creative, trendy, colorful, unique, and easy to use. You have freedom of selecting which ever color suits you. The design must be energetic and attractive.

NAVIGATION

HOME-MUSIC(RnB, Hip hop, Afro pop, POP, dancehall, Reggae)-ARTISTE-NEWS-LOGIN

PAGES REQUIRED
------------
1)Home Page
2)Music

FONTS
GOOGLE FONTS is strongly recommended.

Designers can get inspiration from https://tunabrook.example

Industry/Entity Type

Startup

```html
<!DOCTYPE html>
<html lang="en">
<head>
<meta charset="utf-8">
<title>Vorde Sound</title>
<link href="https://fonts.googleapis.com/css2?family=Barlow:wght@400;500;600;700&display=swap" rel="stylesheet">
<style>
  :root {
    --red: #e60a0a;
    --white: #ffffff;
    --ink: #111111;
    --panel: rgba(0, 0, 0, 0.82);
    --section: #f1f1f1;
    --muted: #555555;
  }
  * { box-sizing: border-box; margin: 0; padding: 0; }
  html, body { width: 1048px; height: 1200px; overflow: hidden; }
  body { position: relative; font-family: "Barlow", Arial, sans-serif; background: var(--white); color: var(--white); }

  .hero { position: absolute; left: 0; top: 0; width: 1048px; height: 620px; overflow: hidden; }
  .hero-photo {
    position: absolute; inset: 0;
    background:
      radial-gradient(ellipse 260px 200px at 930px 120px, rgba(60,140,220,0.55), transparent 70%),
      radial-gradient(ellipse 300px 160px at 820px 560px, rgba(40,120,200,0.6), transparent 70%),
      radial-gradient(ellipse 420px 220px at 480px 470px, rgba(70,70,110,0.55), transparent 70%),
      linear-gradient(180deg, #141320 0%, #1b1a2c 45%, #232338 70%, #15243a 100%);
  }
  .brand { position: absolute; font-weight: 700; letter-spacing: 0.5px; text-transform: uppercase; }
  .hero .brand { left: 126px; top: 28px; font-size: 32px; color: var(--white); }
  .main-nav { position: absolute; top: 40px; left: 529px; }
  .main-nav a { position: absolute; font-size: 12.5px; font-weight: 700; color: var(--white); text-decoration: none; white-space: nowrap; letter-spacing: 0.4px; }
  .login { position: absolute; left: 808px; top: 30px; width: 78px; height: 33px; background: var(--red); color: var(--white); font-size: 12.5px; font-weight: 700; display: flex; align-items: center; justify-content: center; border-radius: 2px; letter-spacing: 0.4px; }

  .signup { position: absolute; left: 126px; top: 130px; width: 316px; height: 454px; background: var(--panel); }
  .signup h1 { position: absolute; left: 18px; top: 20px; font-size: 21px; font-weight: 700; letter-spacing: 0.6px; }
  .field { position: absolute; left: 26px; width: 266px; height: 38px; border: 1px solid #d8d8d8; border-radius: 3px; font-size: 9.5px; font-weight: 600; padding-left: 13px; display: flex; align-items: center; }
  .terms-check { position: absolute; left: 26px; top: 290px; display: flex; align-items: center; font-size: 9px; color: #dddddd; }
  .terms-check span.box { width: 13px; height: 13px; border: 1px solid #cfcfcf; margin-right: 8px; }
  .cta { position: absolute; left: 26px; top: 322px; width: 266px; height: 36px; background: var(--red); font-size: 12.5px; font-weight: 600; display: flex; align-items: center; justify-content: center; letter-spacing: 0.4px; }
  .platforms { position: absolute; left: 27px; top: 385px; font-size: 9px; font-weight: 700; display: flex; align-items: center; gap: 5px; }
  .platforms i { display: inline-block; width: 6px; height: 6px; border-radius: 50%; background: var(--white); }
  .secure { position: absolute; right: 24px; top: 385px; font-size: 9px; font-weight: 700; }
  .terms-link { position: absolute; right: 24px; top: 417px; font-size: 9px; font-weight: 700; text-decoration: underline; }

  .slider-dots { position: absolute; left: 981px; top: 315px; }
  .slider-dots span { position: absolute; left: 0; width: 8px; height: 8px; border-radius: 50%; background: var(--white); }
  .slider-dots span.active { background: var(--red); }

  .genres { position: absolute; left: 0; top: 620px; width: 1048px; height: 497px; background: var(--section); }
  .genre { position: absolute; width: 251px; height: 190px; overflow: hidden; }
  .genre-frame { position: absolute; width: 114px; height: 94px; border: 1px solid rgba(255,255,255,0.75); }
  .genre-title { position: absolute; left: 0; right: 0; top: 14px; text-align: center; font-size: 21px; font-weight: 700; letter-spacing: 0.4px; }
  .download { position: absolute; left: 16px; top: 51px; width: 82px; height: 22px; background: var(--red); font-size: 8.5px; font-weight: 700; display: flex; align-items: center; justify-content: center; letter-spacing: 0.3px; }

  .site-footer { position: absolute; left: 0; top: 1117px; width: 1048px; height: 83px; background: var(--white); color: var(--muted); }
  .site-footer .brand { left: 123px; top: 28px; font-size: 26px; color: var(--ink); }
  .copyright { position: absolute; left: 298px; top: 38px; font-size: 10px; letter-spacing: 0.3px; }
  .footer-nav a { position: absolute; top: 36px; font-size: 13.5px; color: var(--muted); text-decoration: none; letter-spacing: 0.3px; }
</style>
</head>
<body>
  <header class="hero">
    <div class="hero-photo" role="img" aria-label="Rapper performing on a concert stage with microphone under blue stage lights, crowd below"></div>
    <div class="brand">Vorde Sound</div>
    <nav class="main-nav">
      <a style="left:0;top:0">HOME</a>
      <a style="left:62px;top:0">MUSIC</a>
      <a style="left:128px;top:0">ARTISTE</a>
      <a style="left:206px;top:0">NEWS</a>
    </nav>
    <div class="login">LOGIN</div>

    <form class="signup">
      <h1>START YOUR TRAIL</h1>
      <div class="field" style="top:76px">Enter Your Name or E-mail Address</div>
      <div class="field" style="top:128px">Password</div>
      <div class="field" style="top:180px">Re-Enter Your Password</div>
      <div class="field" style="top:231px">Country</div>
      <div class="terms-check"><span class="box"></span>I accept the terms &amp; conditions</div>
      <div class="cta">START YOUR TRAIL</div>
      <div class="platforms">Available <i></i><i></i><i></i></div>
      <div class="secure">Secure Server</div>
      <div class="terms-link">Terms &amp; Conditions</div>
    </form>

    <div class="slider-dots">
      <span class="active" style="top:0"></span>
      <span style="top:19px"></span>
      <span style="top:36px"></span>
      <span style="top:54px"></span>
    </div>
  </header>

  <main class="genres">
    <div class="genre" style="left:126px;top:45px;background:radial-gradient(ellipse at 60% 40%,#3a3a3f,#0b0c0e 70%)" role="img" aria-label="R&amp;B singer with cap performing on stage">
      <div class="genre-frame" style="left:63px;top:45px"><div class="genre-title">RNB</div><div class="download">DOWNLOAD</div></div>
    </div>
    <div class="genre" style="left:398px;top:45px;background:radial-gradient(ellipse at 50% 50%,#2b2f8a,#10126a 75%)" role="img" aria-label="Hip-hop artist in cap singing into a microphone">
      <div class="genre-frame" style="left:69px;top:48px"><div class="genre-title">HIP-HOP</div><div class="download">DOWNLOAD</div></div>
    </div>
    <div class="genre" style="left:670px;top:45px;background:radial-gradient(ellipse at 55% 45%,#8a5a55,#5b2e2c 75%)" role="img" aria-label="Afro pop artist wearing headphones in a colourful shirt">
      <div class="genre-frame" style="left:54px;top:48px"><div class="genre-title">AFRO POP</div><div class="download">DOWNLOAD</div></div>
    </div>
    <div class="genre" style="left:126px;top:258px;background:radial-gradient(ellipse at 40% 40%,#2a2c38,#10121c 75%)" role="img" aria-label="Pop performer in a hat singing in the dark">
      <div class="genre-frame" style="left:63px;top:45px"><div class="genre-title">POP</div><div class="download">DOWNLOAD</div></div>
    </div>
    <div class="genre" style="left:398px;top:258px;background:radial-gradient(ellipse at 50% 40%,#2e3040,#111320 75%)" role="img" aria-label="Dancehall dancer on a dark stage">
      <div class="genre-frame" style="left:49px;top:48px;width:152px"><div class="genre-title">DANCEHALL</div><div class="download" style="left:35px">DOWNLOAD</div></div>
    </div>
    <div class="genre" style="left:670px;top:258px;background:radial-gradient(ellipse at 55% 25%,#2d4f8c,#0c1426 75%)" role="img" aria-label="Reggae singers performing under blue stage light">
      <div class="genre-frame" style="left:54px;top:48px;width:143px"><div class="genre-title">REGGAE</div><div class="download" style="left:30px">DOWNLOAD</div></div>
    </div>
  </main>

  <footer class="site-footer">
    <div class="brand">Vorde Sound</div>
    <div class="copyright">© 2017 COMPANY NAME &nbsp;|&nbsp; ALL RIGHTS RESERVED</div>
    <nav class="footer-nav">
      <a style="left:682px">HOME</a>
      <a style="left:748px">MUSIC</a>
      <a style="left:817px">ARTISTE</a>
      <a style="left:897px">NEWS</a>
    </nav>
  </footer>
</body>
</html>
```